8x8 Social Media Ad - Brant Summit Expo

Attention Real Estate Agents
Please join us for our
Quarterly Real Estate Training Expo
The 2nd Saturday of February, May, August and November
Our Next Training Expo is _________________________________
From 9 am to 1 pm
at
Halvorne Suites Millbrook Court
4817 Copper Willow Lane, Dunmere, MD 20588
Scheduled Speakers
9:00 am - Marcus Pellington - Orientation
9:30 am - Derrin Oakfield - Multiple Income Streams / Crest Program
10:00 am - Talia Brennick - Marketing though Social Media
10:45 am - Rex Dunmore - Generating Business through Ru-Plaza
11:30 am - Kemi Adeyoro - Real Estate Investing
12:15 pm - Gregor Tamsey - (Main Speaker) Training Topic TBA
For more information call Marcus Pellington at (240) 555-0183 or email mpellington@brantsummithomes.example

```html
<!DOCTYPE html>
<html lang="en">
<head>
<meta charset="utf-8">
<title>Brant Summit Expo – Quarterly Real Estate Training Expo</title>
<link rel="stylesheet" href="https://fonts.googleapis.com/css2?family=Barlow:wght@400;500;600;700;800&family=Barlow+Semi+Condensed:wght@400;600;700&display=swap">
<style>
  :root {
    --teal: #1797a0;
    --teal-dark: #0f8790;
    --ink: #111111;
    --paper: #ffffff;
    --backdrop: #d1d2d4;
    --photo-a: #8a9aa3;
    --photo-b: #4c5a63;
  }
  * { margin: 0; padding: 0; box-sizing: border-box; }
  html, body { width: 1200px; height: 1010px; overflow: hidden; background: var(--backdrop); }
  body { font-family: "Barlow", Arial, sans-serif; position: relative; }

  .ad { position: absolute; left: 199px; top: 105px; width: 802px; height: 802px; background: var(--paper); overflow: hidden; }
  .ad svg.frame { position: absolute; left: 0; top: 0; }

  .brand { position: absolute; left: 28px; top: 72px; display: flex; align-items: center; gap: 10px; }
  .brand-mark { width: 26px; height: 26px; background: var(--teal); }
  .brand-name { font-weight: 800; font-size: 17px; color: var(--ink); text-transform: uppercase; line-height: 1.1; }

  .attention { position: absolute; left: 352px; top: 29px; font-weight: 700; font-size: 24px; letter-spacing: .3px; color: var(--teal); white-space: nowrap; }
  .headline { position: absolute; left: 352px; top: 64px; color: var(--paper); text-transform: uppercase; white-space: nowrap; }
  .headline .invite { font-weight: 400; font-size: 26px; letter-spacing: .6px; line-height: 32px; }
  .headline .title { font-weight: 800; font-size: 31px; line-height: 36px; letter-spacing: .3px; }

  .section-label { position: absolute; left: 0; width: 802px; top: 190px; text-align: center; font-weight: 800; font-size: 19px; letter-spacing: .6px; color: var(--ink); }

  .photo { position: absolute; border-radius: 50%; border: 4px solid var(--paper); background: radial-gradient(circle at 50% 40%, var(--photo-a), var(--photo-b)); box-shadow: 0 0 0 1px rgba(0,0,0,.08); }

  .slot { position: absolute; font-family: "Barlow", Arial, sans-serif; color: var(--ink); white-space: nowrap; }
  .slot .time { font-weight: 700; font-size: 15.5px; color: var(--paper); margin-bottom: 12px; line-height: 18px; }
  .slot .name { font-weight: 700; font-size: 15.5px; line-height: 18px; }
  .slot .topic { font-weight: 400; font-size: 14px; line-height: 17px; }

  .keynote { position: absolute; left: 619px; top: 474px; font-family: "Barlow", Arial, sans-serif; color: var(--ink); white-space: nowrap; }
  .keynote .time { font-weight: 700; font-size: 19px; line-height: 22px; }
  .keynote .name { font-weight: 700; font-size: 19px; line-height: 22px; }
  .keynote .topic { font-size: 16.5px; line-height: 20px; }

  .schedule { position: absolute; left: 34px; top: 612px; color: var(--paper); font-size: 15.5px; letter-spacing: .3px; text-transform: uppercase; line-height: 19px; white-space: nowrap; }
  .schedule strong { font-weight: 800; }
  .schedule .rule { width: 532px; height: 1px; background: #bbbbbb; margin: 8px 0 8px; }

  .contact { position: absolute; left: 32px; top: 733px; color: var(--paper); font-size: 18px; line-height: 26px; white-space: nowrap; }
  .contact .lead { font-weight: 700; text-transform: uppercase; letter-spacing: .4px; }
  .contact .line { font-weight: 400; font-size: 17px; letter-spacing: .2px; }
  .contact .line strong { font-weight: 700; }
</style>
</head>
<body>
<main class="ad">
  <svg class="frame" width="802" height="802" viewBox="0 0 802 802" aria-hidden="true">
    <polygon points="291,0 802,0 802,23 288,23" fill="var(--teal)"/>
    <polygon points="270,58 802,58 802,179 248,179" fill="var(--teal)"/>
    <rect x="0" y="201" width="283" height="4" fill="var(--ink)"/>
    <rect x="518" y="201" width="284" height="4" fill="var(--ink)"/>
    <rect x="0" y="225" width="802" height="370" fill="var(--teal)"/>
    <g fill="var(--paper)">
      <rect x="70" y="283" width="230" height="62"/>
      <rect x="325" y="283" width="260" height="62"/>
      <rect x="70" y="395" width="230" height="62"/>
      <rect x="325" y="395" width="230" height="62"/>
      <rect x="70" y="510" width="520" height="52"/>
    </g>
    <g fill="#8fd0d5">
      <rect x="70" y="279" width="230" height="2"/>
      <rect x="325" y="279" width="260" height="2"/>
      <rect x="70" y="391" width="230" height="2"/>
      <rect x="325" y="391" width="230" height="2"/>
      <rect x="70" y="506" width="520" height="2"/>
    </g>
    <circle cx="733" cy="437" r="190" fill="var(--paper)" stroke="var(--teal)" stroke-width="3"/>
    <rect x="0" y="603" width="802" height="110" fill="var(--ink)"/>
    <rect x="0" y="720" width="802" height="82" fill="var(--teal)"/>
  </svg>

  <div class="brand">
    <span class="brand-mark"></span>
    <span class="brand-name">Brant Summit<br>Realty Group</span>
  </div>

  <p class="attention">ATTENTION REAL ESTATE AGENTS</p>
  <h1 class="headline">
    <span class="invite">Please join us for our</span><br>
    <span class="title">Quarterly Real Estate<br>Training Expo</span>
  </h1>

  <h2 class="section-label">SCHEDULED SPEAKERS</h2>

  <div class="photo" role="img" aria-label="Portrait of Marcus Pellington" style="left:15px;top:247px;width:106px;height:106px;"></div>
  <div class="photo" role="img" aria-label="Portrait of Derrin Oakfield" style="left:269px;top:247px;width:106px;height:106px;"></div>
  <div class="photo" role="img" aria-label="Portrait of Talia Brennick" style="left:15px;top:359px;width:106px;height:106px;"></div>
  <div class="photo" role="img" aria-label="Portrait of Rex Dunmore" style="left:269px;top:363px;width:106px;height:106px;"></div>
  <div class="photo" role="img" aria-label="Portrait of Kemi Adeyoro" style="left:15px;top:471px;width:106px;height:106px;"></div>
  <div class="photo" role="img" aria-label="Portrait of Gregor Tamsey, main speaker" style="left:566px;top:240px;width:226px;height:226px;border:5px solid var(--teal);"></div>

  <div class="slot" style="left:127px;top:258px;"><p class="time">9:00 am</p><p class="name">Marcus Pellington</p><p class="topic">Orientation</p></div>
  <div class="slot" style="left:389px;top:258px;"><p class="time">9:30 am</p><p class="name">Derrin Oakfield</p><p class="topic">Multiple Income<br>Streams / Crest Program</p></div>
  <div class="slot" style="left:127px;top:367px;"><p class="time">10:00 am</p><p class="name">Talia Brennick</p><p class="topic">Marketing though<br>Social Media</p></div>
  <div class="slot" style="left:387px;top:367px;"><p class="time">10:45 am</p><p class="name">Rex Dunmore</p><p class="topic">Generating Business<br>through Ru-Plaza</p></div>
  <div class="slot" style="left:133px;top:485px;"><p class="time">11:30 am</p><p class="name">Kemi Adeyoro</p><p class="topic">Real Estate Investing</p></div>

  <div class="keynote">
    <p class="time">12:15 pm</p>
    <p class="name">Gregor Tamsey</p>
    <p class="topic">(Main Speaker)<br>Training Topic TBA</p>
  </div>

  <div class="schedule">
    <p><strong>The 2nd Saturday of February, May, August and November</strong><br>Our next training expo is.</p>
    <div class="rule"></div>
    <p><strong>From 9 am to 1 pm</strong> at Halvorne Suites Millbrook Court<br>4817 Copper Willow Lane, Dunmere, MD 20588</p>
  </div>

  <div class="contact">
    <p class="lead">For more information call</p>
    <p class="line">MARCUS PELLINGTON at <strong>(240) 555-0183</strong> or email <strong>mpellington@brantsummithomes.example</strong></p>
  </div>
</main>
</body>
</html>
```